BOLD & MINIMALIST DESIGN NEEDED

We want a very bold but minimalistic business card design that is impactful and utilizes both sides of the business card. Our current logo is included for your use.

We want bold fonts and good use of negative space. We don't want the logo to overpower the design.

Target Market(s)

Professionals who are building new commercial buildings.

Industry/Entity Type

Construction

Contact Information for Business Card

Name, Title, email, office phone, cell phone, website

Font styles to use
Serif
Sans Serif

Requirements
Must have
• Bold design!

```html
<!DOCTYPE html>
<html lang="en">
<head>
<meta charset="utf-8">
<title>Ridgeline Design + Build — Business Card</title>
<link href="https://fonts.googleapis.com/css2?family=Montserrat:wght@400;700;800&display=swap" rel="stylesheet">
<style>
  :root {
    --backdrop: #959595;
    --brand-green: #84c443;
    --card-black: #141414;
    --white: #ffffff;
    --text-light: #f2f2f2;
  }
  * { margin: 0; padding: 0; box-sizing: border-box; }
  html, body {
    width: 1200px; height: 1108px; overflow: hidden;
    background: var(--backdrop);
    font-family: "Montserrat", Arial, sans-serif;
  }
  .canvas { position: relative; width: 1200px; height: 1108px; }
  .card {
    position: absolute; left: 241px; width: 716px; height: 409px;
    border-radius: 26px; overflow: hidden;
  }
  .card-front { top: 119px; background: var(--brand-green); }
  .card-back { top: 580px; background: var(--card-black); }

  .brand-name {
    position: absolute; left: 0; right: 0;
    display: flex; align-items: center; justify-content: center; gap: 14px;
    color: var(--white); font-weight: 800;
    white-space: nowrap; letter-spacing: 0.04em; line-height: 1;
  }
  .brand-mark { background: var(--white); flex: none; }
  .card-front .brand-name { top: 50%; transform: translateY(-50%); font-size: 30px; }
  .card-front .brand-mark { width: 26px; height: 26px; }
  .card-back .brand-name { top: 98px; font-size: 24px; }
  .card-back .brand-mark { width: 20px; height: 20px; }

  .holder {
    position: absolute; right: 388px; top: 244px; text-align: right;
  }
  .holder-name {
    color: var(--brand-green); font-weight: 700; font-size: 32px;
    letter-spacing: 0.01em; line-height: 1; white-space: nowrap;
  }
  .holder-title {
    margin-top: 14px; color: var(--text-light); font-size: 18px; line-height: 1;
  }
  .divider {
    position: absolute; left: 355px; top: 224px; width: 2px; height: 102px;
    background: var(--brand-green);
  }
  .contact-list {
    position: absolute; left: 384px; top: 220px; list-style: none;
  }
  .contact-item {
    display: flex; align-items: center; gap: 10px;
    height: 28.5px; color: var(--text-light); font-size: 18px;
    letter-spacing: 0.02em; white-space: nowrap;
  }
  .contact-item svg { width: 16px; height: 16px; flex: none; fill: var(--brand-green); }
  .address-band {
    position: absolute; left: 0; right: 0; top: 359px; height: 25px;
    background: var(--brand-green); color: var(--white);
    font-size: 17px; line-height: 25px; text-align: center;
  }
</style>
</head>
<body>
<main class="canvas">
  <section class="card card-front">
    <div class="brand-name"><span class="brand-mark"></span><span>RIDGELINE DESIGN + BUILD</span></div>
  </section>

  <section class="card card-back">
    <div class="brand-name"><span class="brand-mark"></span><span>RIDGELINE DESIGN + BUILD</span></div>

    <div class="holder">
      <p class="holder-name">MARCUS HALE</p>
      <p class="holder-title">OWNER-CEO</p>
    </div>

    <div class="divider"></div>

    <ul class="contact-list">
      <li class="contact-item">
        <svg viewBox="0 0 16 16" aria-hidden="true"><path d="M1 6c0-2 3-3 7-3s7 1 7 3v1h-3V5.5C11 5 10 5 8 5S5 5 4 5.5V7H1z"/><rect x="3" y="8" width="10" height="6" rx="1"/></svg>
        123 456 789
      </li>
      <li class="contact-item">
        <svg viewBox="0 0 16 16" aria-hidden="true"><path d="M4 1h8v14H4zM5.5 2.5v9h5v-9z"/><circle cx="8" cy="13.2" r="0.8" fill="#141414"/></svg>
        123 456 789
      </li>
      <li class="contact-item">
        <svg viewBox="0 0 16 16" aria-hidden="true"><path d="M1 3h14v10H1zM2.5 4.5 8 9l5.5-4.5v-.2h-11z"/></svg>
        info@yourgmail.com
      </li>
      <li class="contact-item">
        <svg viewBox="0 0 16 16" aria-hidden="true"><circle cx="8" cy="8" r="7"/><path d="M4 4c2 1 2 3 1 4s1 3 2 4M10 3c-1 2 1 3 3 3" stroke="#141414" stroke-width="1.2" fill="none"/></svg>
        www.yourwebsite.com
      </li>
    </ul>

    <div class="address-band">Your address, City State, Zip 1234</div>
  </section>
</main>
</body>
</html>
```